Lumvra App | Pre-Launch Homepage

Dear designer,
Lumvra is a soon to be launched innovative & free social platform for collaborative addictions quitting.
We require a design for our pre-launch homepage that will elevate our basic wireframes to the next level.
We would like the wireframes to serve as a guideline only, and not as a final version of the design. If you have cool ideas - we would appreciate your creativity!
* This is a pre-launch website for a mobile app, and as such the design must be consistent with the general style, design and atmosphere of the app (see screenshot in the shared Drive link).
* We liked the style and feel of the following website: http://tandelhub.example/ - Please let's use it as a reference as well.
* The existing text in the wireframes is there just to represent a place for text. Copy will be edited by us after the design is done.
Please find the wireframes attached, and all relevant design assets and app screenshots in the following Drive shared link -
https://files.example-share.net/open?id=7KQ204RtP3mNxa8Y2Lb61H9cdVzQ
Thanks,
Reginald
Industry/Entity Type
Social
Number of Pages Required
1 page
Look and feel
Each slider illustrates characteristics of the customer's brand and the style your logo design should communicate.

```html
<!DOCTYPE html>
<html lang="en">
<head>
<meta charset="utf-8">
<title>Lumvra App | Pre-Launch Homepage</title>
<link rel="stylesheet" href="https://fonts.googleapis.com/css2?family=Open+Sans:wght@300;400;600;700&family=Oswald:wght@400;500&display=swap">
<style>
:root{
  --orange:#f5a11c;
  --orange-deep:#e8890c;
  --ink:#2b2b2b;
  --dark:#1e1f21;
  --dark-2:#2c2d30;
  --grey:#6f6f6f;
  --grey-light:#9a9a9a;
  --line:#e3e3e3;
  --paper:#ffffff;
  --footer:#efefef;
  --white:#ffffff;
}
*{margin:0;padding:0;box-sizing:border-box}
html,body{width:1200px;height:3540px;overflow:hidden}
body{font-family:"Open Sans",Arial,sans-serif;color:var(--ink);background:var(--paper);position:relative}
section,footer{position:absolute;left:0;width:1200px;overflow:hidden}
.abs{position:absolute}
.photo{position:absolute;inset:0}

/* hero */
.hero{top:0;height:600px}
.hero .photo{background:linear-gradient(120deg,#2a221c 0%,#4a3a2c 45%,#6b5846 70%,#3b3028 100%)}
.hero-nav{top:22px;left:0;width:1200px;height:40px}
.menu-btn{left:24px;top:0;width:32px;height:32px;border:2px solid var(--white);border-radius:50%}
.nav-contact{right:86px;top:6px;color:var(--white);font-size:14px;letter-spacing:1px}
.phone-btn{right:40px;top:0;width:32px;height:32px;border:2px solid var(--white);border-radius:50%}
.brand{left:88px;top:82px;font-size:72px;font-weight:700;color:var(--orange);line-height:1}
.hero-title{left:88px;top:168px;font-family:"Oswald",sans-serif;font-weight:500;font-size:36px;color:var(--white);letter-spacing:.5px}
.hero-sub{left:88px;top:222px;width:380px;font-size:14px;color:#e6e0d8;line-height:1.5}
.hero-label{left:88px;top:300px;font-size:13px;color:#f0ebe4;letter-spacing:.5px}
.field{height:38px;border:1px solid rgba(255,255,255,.4);background:rgba(255,255,255,.08);color:#cfc6bb;font-size:12px;padding:11px 14px}
.btn{height:38px;background:var(--orange);color:var(--white);font-size:12px;font-weight:700;letter-spacing:1px;text-align:center;line-height:38px}
.hero-field{left:88px;top:336px;width:330px}
.hero-btn{left:426px;top:336px;width:140px}
.slider-dots{left:570px;top:572px;display:flex;gap:10px}
.slider-dots span{width:10px;height:10px;border-radius:50%;background:rgba(255,255,255,.5)}
.slider-dots span:first-child{background:var(--orange)}

/* features */
.features{top:600px;height:480px;background:var(--paper)}
.section-title{width:1200px;text-align:center;font-weight:300;font-size:34px;color:#444;letter-spacing:2px}
.features .section-title{top:94px}
.feature{width:280px;text-align:center}
.feature-icon{width:84px;height:84px;margin:0 auto}
.feature h3{margin-top:24px;font-size:14px;font-weight:600;color:#555;letter-spacing:1px}
.feature p{margin-top:14px;font-size:12px;color:var(--grey-light);line-height:1.6}

/* fun */
.fun{top:1080px;height:460px}
.fun .photo{background:linear-gradient(160deg,#3a3b3e 0%,#1b1c1e 55%,#121213 100%)}
.block-title{font-size:46px;font-weight:400;color:var(--white);letter-spacing:1px}
.block-lead{font-size:14px;color:#cfcfcf}
.block-text{font-size:13px;color:#a8a8a8;line-height:1.7}
.outline-btn{border:1px solid #cfcfcf;color:var(--white);font-size:12px;letter-spacing:1px;padding:9px 18px}

/* inspire */
.inspire{top:1540px;height:320px;background:var(--paper)}
.inspire .block-title{color:var(--orange)}
.inspire .block-lead{color:#555}
.inspire .block-text{color:#8a8a8a}
.tick-list{list-style:none}
.tick-list li{font-size:13px;color:var(--orange);margin-bottom:14px;display:flex;align-items:center;gap:12px}

/* achieve */
.achieve{top:1860px;height:580px}
.achieve .photo{background:linear-gradient(180deg,#2a2b2e 0%,#1c1d1f 100%)}
.achieve .section-title{top:40px;color:var(--white);font-weight:400}
.achieve-text{top:108px;left:300px;width:600px;text-align:center;font-size:17px;color:#dcdcdc;line-height:1.6}
.achieve-note{top:178px;left:300px;width:600px;text-align:center;font-size:14px;color:#bdbdbd}
.perk{width:300px}
.perk h4{font-size:15px;font-weight:400;color:var(--white)}
.perk p{margin-top:8px;font-size:12px;color:#9d9d9d;line-height:1.6}
.perk-icon{width:58px;height:58px;border:2px solid #8c8c8c;border-radius:50%}

/* coming soon */
.coming{top:2440px;height:600px;background:var(--paper)}
.coming .section-title{top:56px;font-weight:400;color:#333}
.coming-text{top:118px;left:200px;width:800px;text-align:center;font-size:12px;color:var(--grey-light);line-height:1.6}
.store-badges{top:176px;left:520px;display:flex;gap:22px}
.store-badges span{width:40px;height:40px;border-radius:8px;background:#d0d0d0}
.tablet{left:300px;top:262px;width:600px;height:420px;background:#2b2c2f;border-radius:34px}
.tablet-screen{left:40px;top:40px;width:520px;height:380px;background:linear-gradient(180deg,#dfe3e6 0%,#c9ced2 100%)}
.app-name{left:240px;top:18px;font-size:16px;font-weight:700;color:#444}
.avatar{left:216px;top:80px;width:90px;height:90px;border-radius:50%;background:linear-gradient(160deg,#b59a86,#7a6556);border:4px solid var(--white)}
.welcome{left:0;top:186px;width:520px;text-align:center;font-size:26px;color:#333}
.arrow{top:290px;width:30px;height:60px}

/* notify */
.notify{top:3040px;height:400px}
.notify .photo{background:linear-gradient(120deg,#3a3431 0%,#24211f 50%,#171615 100%)}
.notify-icon{left:576px;top:42px;width:48px;height:48px;border-radius:50%;background:var(--white)}
.notify-title{top:104px;width:1200px;text-align:center;font-family:"Oswald",sans-serif;font-weight:500;font-size:46px;color:var(--white)}
.notify-sub{top:176px;width:1200px;text-align:center;font-size:14px;color:#cfcfcf}
.notify-field{left:268px;top:218px;width:500px;height:56px;padding:18px 20px;font-size:14px;background:var(--white);color:#aaa;border:none}
.notify-btn{left:768px;top:218px;width:166px;height:56px;line-height:56px;font-size:14px}

/* footer */
.site-footer{top:3440px;height:100px;background:var(--footer)}
.copyright{left:40px;top:42px;font-size:12px;color:#8a8a8a}
.social{right:40px;top:34px;display:flex;gap:10px}
.social span{width:30px;height:30px;border-radius:50%;background:#b8b8b8}
</style>
</head>
<body>

<section class="hero">
  <div class="photo" role="img" aria-label="Photo of a hand holding a smartphone showing the app, over a dark warm background"></div>
  <svg class="abs" style="left:0;top:0" width="1200" height="600" aria-hidden="true">
    <polygon points="1010,0 1200,0 1200,600 790,600" fill="var(--orange)"/>
    <g transform="rotate(8 950 300)">
      <rect x="880" y="40" width="160" height="320" rx="22" fill="#f4f4f4"/>
      <rect x="892" y="80" width="136" height="240" fill="#262626"/>
      <circle cx="960" cy="340" r="10" fill="none" stroke="#bbb" stroke-width="2"/>
    </g>
  </svg>
  <div class="abs hero-nav">
    <div class="abs menu-btn">
      <svg width="28" height="28" viewBox="0 0 28 28" aria-hidden="true"><path d="M9 10h10M9 14h10M9 18h10" stroke="#fff" stroke-width="2"/></svg>
    </div>
    <div class="abs nav-contact">CONTACT US</div>
    <div class="abs phone-btn">
      <svg width="28" height="28" viewBox="0 0 28 28" aria-hidden="true"><path d="M10 8l3 0 1 4-2 1q1 3 4 4l1-2 4 1 0 3q-9 1-11-11z" fill="#fff"/></svg>
    </div>
  </div>
  <div class="abs brand">Lumvra</div>
  <h1 class="abs hero-title">BECOME A BETTER VERSION OF YOURSELF</h1>
  <p class="abs hero-sub">Lumvra is a revolutionary &amp; free social platform for collaborative addictions quitting.</p>
  <p class="abs hero-label">SUBSCRIBE BELOW FOR THE BETA RELEASE AND UPDATES</p>
  <div class="abs field hero-field">Enter your email address</div>
  <div class="abs btn hero-btn">LET ME KNOW</div>
  <div class="abs slider-dots"><span></span><span></span><span></span></div>
</section>

<section class="features">
  <h2 class="abs section-title">LUMVRA FEATURES</h2>
  <div class="abs feature" style="left:180px;top:170px">
    <svg class="feature-icon" viewBox="0 0 84 84" aria-hidden="true">
      <circle cx="42" cy="42" r="34" fill="none" stroke="#d8322b" stroke-width="18"/>
      <circle cx="42" cy="42" r="34" fill="none" stroke="#fff" stroke-width="18" stroke-dasharray="18 35.4" stroke-dashoffset="9"/>
      <circle cx="42" cy="42" r="43" fill="none" stroke="#333" stroke-width="2"/>
      <circle cx="42" cy="42" r="25" fill="none" stroke="#333" stroke-width="2"/>
    </svg>
    <h3>NEVER BE ALONE</h3>
    <p>Lorem ipsum dolor sit amet consectetur adipiscing elit sed do eiusmod tempor incididunt ut labore et dolore magna aliqua.</p>
  </div>
  <div class="abs feature" style="left:468px;top:170px">
    <svg class="feature-icon" viewBox="0 0 84 84" aria-hidden="true">
      <polygon points="42,4 52,32 82,32 58,50 67,80 42,62 17,80 26,50 2,32 32,32" fill="#f2b632" stroke="#b37a12" stroke-width="2"/>
    </svg>
    <h3>NETWORK POWER</h3>
    <p>Lorem ipsum dolor sit amet consectetur adipiscing elit sed do eiusmod tempor incididunt ut labore et dolore magna aliqua.</p>
  </div>
  <div class="abs feature" style="left:772px;top:170px">
    <div class="feature-icon" role="img" aria-label="Illustrated icon for staying motivated" style="background:radial-gradient(circle,#6a6a6a 0%,#3a3a3a 70%,transparent 71%)"></div>
    <h3>STAY MOTIVATED</h3>
    <p>Lorem ipsum dolor sit amet consectetur adipiscing elit sed do eiusmod tempor incididunt ut labore et dolore magna aliqua.</p>
  </div>
</section>

<section class="fun">
  <div class="photo" role="img" aria-label="Dark moody background photo"></div>
  <svg class="abs" style="left:250px;top:70px" width="170" height="330" aria-hidden="true">
    <g transform="rotate(-6 85 165)">
      <rect x="15" y="10" width="140" height="300" rx="20" fill="#111"/>
      <rect x="25" y="50" width="120" height="210" fill="var(--orange)"/>
      <circle cx="85" cy="155" r="34" fill="none" stroke="#fff" stroke-width="6"/>
      <rect x="62" y="148" width="46" height="12" fill="#fff"/>
      <line x1="61" y1="131" x2="109" y2="179" stroke="#fff" stroke-width="6"/>
    </g>
  </svg>
  <h2 class="abs block-title" style="left:560px;top:92px">FUN</h2>
  <p class="abs block-lead" style="left:560px;top:156px">Duis aute irure dolor in reprehenderit in voluptate</p>
  <p class="abs block-text" style="left:560px;top:190px;width:400px">Lorem ipsum dolor sit amet consectetur adipiscing elit. Sed do eiusmod tempor incididunt ut labore et dolore magna aliqua enim ad minim veniam quis.</p>
  <p class="abs block-text" style="left:560px;top:266px;width:400px">Nostrud exercitation ullamco laboris nisi ut aliquip ex ea commodo consequat. Duis aute irure dolor in reprehenderit in voluptate velit esse.</p>
  <div class="abs outline-btn" style="left:560px;top:350px">MORE INFO</div>
</section>

<section class="inspire">
  <h2 class="abs block-title" style="left:180px;top:54px">INSPIRE</h2>
  <p class="abs block-lead" style="left:180px;top:112px">Duis aute irure dolor in reprehenderit in voluptate velit esse cillum</p>
  <p class="abs block-text" style="left:180px;top:140px;width:430px">Lorem ipsum dolor sit amet consectetur adipiscing elit sed do eiusmod tempor. Ut enim ad minim veniam quis nostrud exercitation ullamco laboris nisi.</p>
  <ul class="abs tick-list" style="left:180px;top:214px">
    <li><svg width="14" height="14" aria-hidden="true"><rect x="1" y="1" width="12" height="12" fill="none" stroke="var(--orange)"/><path d="M3 7l3 3 5-6" fill="none" stroke="var(--orange)" stroke-width="1.5"/></svg>Duis aute irure dolor in reprehenderit</li>
    <li><svg width="14" height="14" aria-hidden="true"><rect x="1" y="1" width="12" height="12" fill="none" stroke="var(--orange)"/><path d="M3 7l3 3 5-6" fill="none" stroke="var(--orange)" stroke-width="1.5"/></svg>Lorem ipsum dolor sit amet</li>
    <li><svg width="14" height="14" aria-hidden="true"><rect x="1" y="1" width="12" height="12" fill="none" stroke="var(--orange)"/><path d="M3 7l3 3 5-6" fill="none" stroke="var(--orange)" stroke-width="1.5"/></svg>Nemo enim ipsam voluptatem quia voluptas</li>
  </ul>
  <svg class="abs" style="left:690px;top:30px" width="190" height="300" aria-hidden="true">
    <rect x="10" y="0" width="170" height="330" rx="24" fill="#151515"/>
    <rect x="22" y="50" width="146" height="250" fill="var(--orange)"/>
    <circle cx="95" cy="160" r="30" fill="none" stroke="#fff" stroke-width="6"/>
    <rect x="82" y="190" width="26" height="22" fill="#fff"/>
  </svg>
</section>

<section class="achieve">
  <div class="photo" role="img" aria-label="Dark textured background"></div>
  <h2 class="abs section-title">ACHIEVE</h2>
  <p class="abs achieve-text">Lumvra is built as a pyramid of relationships that makes use of the Social Cognitive Theory, to provide a powerful network of positive reinforcement</p>
  <p class="abs achieve-note">The bigger you make it the stronger you get.</p>

  <div class="abs perk" style="left:96px;top:300px;text-align:right;width:290px"><h4>Helping you launch</h4><p>Lumvra is built as a pyramid of relationships that makes use of the Social Cognitive Theory.</p></div>
  <svg class="abs perk-icon" style="left:400px;top:296px" viewBox="0 0 58 58" aria-hidden="true"><path d="M20 38l18-18M28 20h10v10" fill="none" stroke="#ccc" stroke-width="3"/></svg>
  <div class="abs perk" style="left:96px;top:420px;text-align:right;width:290px"><h4>Easy to Customize</h4><p>Lumvra is built as a pyramid of relationships that makes use of the Social Cognitive Theory.</p></div>
  <svg class="abs perk-icon" style="left:400px;top:416px" viewBox="0 0 58 58" aria-hidden="true"><path d="M19 19l20 20M39 19l-20 20" stroke="#ccc" stroke-width="3"/></svg>

  <svg class="abs perk-icon" style="left:742px;top:296px" viewBox="0 0 58 58" aria-hidden="true"><rect x="21" y="16" width="16" height="26" rx="3" fill="none" stroke="#ccc" stroke-width="3"/></svg>
  <div class="abs perk" style="left:816px;top:300px"><h4>Enterprise mobility</h4><p>Lumvra is built as a pyramid of relationships that makes use of the Social Cognitive Theory.</p></div>
  <svg class="abs perk-icon" style="left:742px;top:416px" viewBox="0 0 58 58" aria-hidden="true"><rect x="17" y="17" width="10" height="10" fill="#ccc"/><rect x="31" y="17" width="10" height="10" fill="#ccc"/><rect x="17" y="31" width="10" height="10" fill="#ccc"/><rect x="31" y="31" width="10" height="10" fill="#ccc"/></svg>
  <div class="abs perk" style="left:816px;top:420px"><h4>The Apps Landscape</h4><p>Lumvra is built as a pyramid of relationships that makes use of the Social Cognitive Theory.</p></div>

  <svg class="abs" style="left:470px;top:230px" width="260" height="350" aria-hidden="true">
    <rect x="10" y="60" width="120" height="300" rx="16" fill="#e9e9e9" transform="rotate(-10 70 210)"/>
    <rect x="130" y="60" width="120" height="300" rx="16" fill="#e9e9e9" transform="rotate(10 190 210)"/>
    <rect x="60" y="20" width="140" height="340" rx="18" fill="#f7f7f7"/>
    <rect x="70" y="60" width="120" height="290" fill="var(--orange)"/>
    <text x="130" y="140" text-anchor="middle" font-family="Open Sans, sans-serif" font-weight="700" font-size="26" fill="#fff">Lumvra</text>
    <path d="M112 190h36v14q0 18-18 18t-18-18zM124 222h12v14h10v6h-32v-6h10z" fill="#fff"/>
  </svg>
</section>

<section class="coming">
  <h2 class="abs section-title">COMING SOON</h2>
  <p class="abs coming-text">Lorem ipsum dolor sit amet consectetur adipiscing elit sed do eiusmod tempor incididunt ut labore et dolore magna aliqua. Ut enim ad minim veniam quis nostrud exercitation ullamco laboris nisi ut aliquip ex ea commodo consequat duis aute irure.</p>
  <div class="abs store-badges" aria-label="App store badges"><span></span><span></span><span></span></div>
  <svg class="abs arrow" style="left:238px" viewBox="0 0 30 60" aria-hidden="true"><path d="M24 4L6 30l18 26" fill="none" stroke="#dcdcdc" stroke-width="3"/></svg>
  <svg class="abs arrow" style="left:932px" viewBox="0 0 30 60" aria-hidden="true"><path d="M6 4l18 26L6 56" fill="none" stroke="#dcdcdc" stroke-width="3"/></svg>
  <div class="abs tablet">
    <div class="abs tablet-screen">
      <div class="abs app-name">Lumvra</div>
      <div class="abs avatar" role="img" aria-label="User profile photo"></div>
      <div class="abs welcome">Welcome Marcus!</div>
    </div>
  </div>
</section>

<section class="notify">
  <div class="photo" role="img" aria-label="Dark photo of a person using a phone"></div>
  <svg class="abs notify-icon" viewBox="0 0 48 48" aria-hidden="true"><path d="M13 24l22-10-6 22-5-7z" fill="#333"/></svg>
  <h2 class="abs notify-title">GET NOTIFIED OF ANY UPDATES!</h2>
  <p class="abs notify-sub">Subscribe below for the beta release and updates</p>
  <div class="abs field notify-field">Enter Your Email Address</div>
  <div class="abs btn notify-btn">LET ME KNOW!</div>
</section>

<footer class="site-footer">
  <p class="abs copyright">Copyright © Lumvra Ltd. All rights reserved. Contact Us | Terms | Privacy Policy</p>
  <div class="abs social" aria-label="Social links"><span></span><span></span><span></span><span></span></div>
</footer>

</body>
</html>
```